Modern design company business card design

We are a design oriented construction firm. The owner is an architect and licensed General Contractor and accomplished furniture designer. We do new home construction and large scale remodeling and office design. We would like a design for our new business cards that is clean and modern, but relatable. We like the bright green color of our logo mixed with different shades of grey. We're also open to reinterpreting the logo.

Target Market(s)

Potential design clients,
Construction clients

Industry/Entity Type

Architecture

Contact Information for Business Card

Tall Maple Design | Build Inc. (optional with logo, Inc. optional)Jeffrey MorganOwner (optional)317.555.0148 cell317.431.8056 officejmorgan@greensquareinc.comwww.greensquareinc.com

Font styles to use
Sans Serif
Other font styles liked:
• Avenir

Requirements
Nice to have
• I like designs that have some continuity between the front and back, i.e. similar layouts or graphic elements that wrap around the card. I tend to prefer horizontal over vertical, but that's not a have to. I also tend to prefer white or recycled paper.

```html
<!DOCTYPE html>
<html lang="en">
<head>
<meta charset="utf-8">
<title>Tall Maple Design | Build – Business Card</title>
<link rel="stylesheet" href="https://fonts.googleapis.com/css2?family=Open+Sans:wght@400;600;700&display=swap">
<style>
  :root {
    --backdrop: #e7e7e5;
    --paper: #ffffff;
    --green: #5cbf3a;
    --green-light: #b6e07a;
    --green-dark: #2e9a2c;
    --grey-text: #6d6e70;
    --grey-band: #5a5b5e;
    --grey-dark: #2f3033;
    --grey-mid: #65666a;
    --white: #ffffff;
    --shadow: rgba(0,0,0,.18);
  }
  * { box-sizing: border-box; margin: 0; padding: 0; }
  html, body { width: 1200px; height: 913px; overflow: hidden; }
  body {
    background: var(--backdrop);
    font-family: "Open Sans", sans-serif;
    position: relative;
  }
  .card {
    position: absolute;
    width: 560px;
    height: 320px;
    border-radius: 3px;
    overflow: hidden;
    box-shadow: 0 10px 28px var(--shadow);
  }

  /* ---------- Front ---------- */
  .card-front { left: 70px; top: 110px; background: var(--paper); }
  .front-band-grey {
    position: absolute; left: 0; bottom: 0;
    width: 60%; height: 36px;
    background: var(--grey-band);
  }
  .front-band-green {
    position: absolute; right: 0; bottom: 0;
    width: 42%; height: 92px;
    background: linear-gradient(to top, var(--green-dark) 0%, var(--green) 45%, var(--green-light) 80%, rgba(182,224,122,0) 100%);
  }
  .brand-name {
    font-size: 17px;
    font-weight: 600;
    letter-spacing: 2px;
    line-height: 1.35;
    text-transform: uppercase;
  }
  .front-brand {
    position: absolute;
    left: 48px; top: 150px;
    width: 180px;
    color: var(--grey-text);
  }
  .contact {
    position: absolute;
    left: 250px; top: 70px;
    color: var(--grey-text);
  }
  .contact-name {
    font-size: 17px; font-weight: 700; letter-spacing: .5px;
    text-transform: uppercase;
  }
  .contact-role {
    font-size: 11px; font-weight: 600; letter-spacing: 1px;
    color: var(--green); text-transform: uppercase;
    margin-bottom: 16px;
  }
  .contact-list { list-style: none; }
  .contact-list li {
    display: flex; align-items: center; gap: 8px;
    font-size: 12.5px; line-height: 20px;
  }
  .contact-list svg { width: 11px; height: 11px; flex: none; }

  /* ---------- Back ---------- */
  .card-back {
    left: 570px; top: 480px;
    background: linear-gradient(160deg, var(--grey-mid) 0%, #4a4b4e 45%, var(--grey-dark) 100%);
  }
  .back-brand {
    position: absolute;
    left: 0; right: 0; top: 124px;
    text-align: center;
    color: var(--white);
  }
  .back-brand .brand-name { font-size: 22px; letter-spacing: 3px; }
</style>
</head>
<body>

<section class="card card-front" aria-label="Business card front">
  <div class="front-band-grey"></div>
  <div class="front-band-green"></div>

  <div class="front-brand">
    <p class="brand-name">Tall Maple<br>Design | Build</p>
  </div>

  <div class="contact">
    <p class="contact-name">Dennis Holloway</p>
    <p class="contact-role">Owner</p>
    <ul class="contact-list">
      <li>
        <svg viewBox="0 0 12 12"><rect x="3" y="0.5" width="6" height="11" rx="1" fill="none" stroke="#5cbf3a" stroke-width="1.4"/></svg>
        317.555.0172
      </li>
      <li>
        <svg viewBox="0 0 12 12"><path d="M2 1l2.5 0 1 3-1.5 1a6 6 0 003 3l1-1.5 3 1V10a1.5 1.5 0 01-1.5 1.5A9.5 9.5 0 01.5 2.5 1.5 1.5 0 012 1z" fill="#5cbf3a"/></svg>
        317.555.0148
      </li>
      <li>
        <svg viewBox="0 0 12 12"><circle cx="6" cy="6" r="5" fill="none" stroke="#5cbf3a" stroke-width="1.3"/><path d="M1 6h10M6 1c2 2.5 2 7.5 0 10M6 1c-2 2.5-2 7.5 0 10" fill="none" stroke="#5cbf3a" stroke-width="1"/></svg>
        www.tallmapleinc.example
      </li>
      <li>
        <svg viewBox="0 0 12 12"><rect x="0.5" y="2" width="11" height="8" rx="1" fill="#5cbf3a"/><path d="M1 2.5l5 4 5-4" fill="none" stroke="#fff" stroke-width="1"/></svg>
        dholloway@tallmapleinc.example
      </li>
    </ul>
  </div>
</section>

<section class="card card-back" aria-label="Business card back">
  <div class="back-brand">
    <p class="brand-name">Tall Maple<br>Design | Build</p>
  </div>
</section>

</body>
</html>
```